Online business manager needs a website

I need a website designed and then coded. I am an online business manager serving a number of different industries providing administrative support to existing small businesses and helping solo practitioners get their new business up and running.

I didn't have a logo formally designed but have been using the attached avatar and wouldn't mind something that incorporated that.

The business doesn't have an official name, so I've just been using my name Lena Morvath, Online Business Manager or Lena Morvath, OBM. I've attached two documents that I have made previously for an example of content.

I would prefer the final site be in Wordpress.

Requirements
Must have
• A way to contact me, testimonials, list of services

```html
<!DOCTYPE html>
<html lang="en">
<head>
<meta charset="utf-8">
<title>Lena Morvath, OBM</title>
<link rel="stylesheet" href="https://fonts.googleapis.com/css2?family=Poppins:wght@400;500;600;700&family=Kumbh+Sans:wght@400;500;600&display=swap">
<style>
:root{
  --purple-dark:#4a2173;
  --purple:#5e2683;
  --purple-bright:#7e2a8b;
  --ink:#111111;
  --paper:#ffffff;
  --card:#faf8fc;
  --line:#cfcfd6;
  --black:#000000;
}
*{box-sizing:border-box;margin:0;padding:0}
html,body{width:1200px;height:4580px;overflow:hidden}
body{position:relative;background:var(--paper);font-family:"Kumbh Sans",sans-serif;color:var(--ink)}
.abs{position:absolute}
h2{font-family:"Poppins",sans-serif;font-weight:700;letter-spacing:4px;font-size:33px}

/* header */
.brand{left:110px;top:10px;width:235px;color:var(--purple-bright);font-family:"Poppins",sans-serif;font-weight:500;white-space:nowrap;z-index:2}
.brand-name{font-size:24px;letter-spacing:1.5px;line-height:32px}
.brand-tag{font-size:19px;letter-spacing:3px;line-height:22px}
.nav{left:357px;top:0;width:843px;height:71px;background:var(--purple-dark);border-bottom-left-radius:40px;display:flex;align-items:center;padding-left:52px;white-space:nowrap}
.nav a{color:#fff;text-decoration:none;font-family:"Poppins",sans-serif;font-size:15px;letter-spacing:1.5px;margin-right:52px}
.nav .login{background:#fff;color:var(--ink);padding:4px 20px;margin-left:-20px;margin-right:0;font-size:15px}

/* hero */
.hero-edge{left:0;top:88px;width:1200px;height:652px;background:var(--purple-dark);clip-path:polygon(0 0,100% 0,100% 80%,50% 100%,0 80%)}
.hero-photo{left:0;top:88px;width:1200px;height:652px;background:linear-gradient(100deg,#3b1e63 0%,#6a4a8e 45%,#a88a9a 75%,#cfa37a 100%);clip-path:polygon(0 0,100% 0,100% 77%,50% 96%,0 77%)}
.hero-title{left:113px;top:268px;color:#fff;font-family:"Poppins",sans-serif;font-weight:600;letter-spacing:6px;white-space:nowrap}
.hero-title .small{font-size:42px;line-height:54px}
.hero-title .big{font-size:52px;line-height:62px}
.btn-light{left:115px;top:470px;width:166px;height:43px;background:#fff;border-radius:4px;font-family:"Poppins",sans-serif;font-size:15px;letter-spacing:2px;display:flex;align-items:center;justify-content:center}
.arrow{width:46px;height:24px}

/* about */
.about-title{left:112px;top:818px}
.about-text{left:112px;top:876px;width:492px;font-size:15px;line-height:31px;letter-spacing:1.6px}
.btn-dark{left:112px;top:1146px;width:130px;height:41px;background:var(--purple-dark);color:#fff;border-radius:5px;font-family:"Poppins",sans-serif;font-size:15px;letter-spacing:2px;display:flex;align-items:center;justify-content:center}
.about-frame{left:635px;top:832px;width:462px;height:395px;border:6px solid var(--purple-dark);border-radius:0 90px 0 90px}
.about-photo{left:658px;top:841px;width:414px;height:379px;background:linear-gradient(160deg,#c2407e,#8a3563 50%,#4d5a3a)}

/* services */
.services{left:0;top:1333px;width:1200px;height:605px;background:linear-gradient(135deg,var(--purple-dark) 0%,var(--purple) 50%,var(--purple-bright) 100%);clip-path:polygon(0 22%,50% 0,100% 22%,100% 100%,0 100%)}
.services-title{top:1430px;width:1200px;text-align:center;color:#fff}
.service{width:240px;text-align:center;color:#fff}
.service .circle{width:199px;height:199px;border-radius:50%;background:#fff;margin:0 auto;display:flex;align-items:center;justify-content:center}
.service .label{font-family:"Poppins",sans-serif;font-size:15px;letter-spacing:2px;line-height:20px;height:44px;margin-top:34px;display:flex;align-items:center;justify-content:center}
.service svg.arrow{margin-top:8px}

/* rates */
.rates-title{top:2025px;width:1200px;text-align:center}
.rate{width:288px;height:430px;top:2126px}
.rate svg{position:absolute;left:0;top:0}
.rate .head{position:absolute;top:34px;width:100%;text-align:center;font-family:"Poppins",sans-serif;font-size:16px;letter-spacing:2px}
.rate .desc{position:absolute;top:128px;left:49px;width:190px;text-align:center;font-size:17px;line-height:31px;letter-spacing:1.5px}
.rate .price{position:absolute;top:247px;left:94px;width:100px;height:100px;border-radius:50%;background:var(--purple-dark);color:#fff;display:flex;align-items:center;justify-content:center;font-family:"Poppins",sans-serif;font-size:22px;letter-spacing:1px}
.rate.featured .head,.rate.featured .desc{color:#fff}
.rate.featured .price{background:#fff;color:var(--ink)}

/* testimonials */
.testi{left:0;top:2653px;width:1200px;height:494px;background:linear-gradient(180deg,#5b3c85 0%,#4c2a78 50%,#3f1f6b 100%);clip-path:polygon(0 0,100% 0,100% 75%,50% 100%,0 75%)}
.testi-title{top:2712px;width:1200px;text-align:center;color:#fff}
.quote{left:120px;top:2782px;width:960px;text-align:center;color:#fff;font-size:15px;line-height:31px;letter-spacing:1.5px}
.cite{top:2896px;width:1200px;text-align:center;color:#fff;font-size:13px;letter-spacing:1.5px}
.avatar{left:552px;top:2942px;width:96px;height:96px;border-radius:50%;background:linear-gradient(140deg,#d6a070,#7b4a3a);border:3px solid #6e5a84}

/* skills */
.skills-title{top:3230px;width:1200px;text-align:center}
.skill{width:267px;height:89px}
.skill .pill{position:absolute;left:40px;top:20px;width:227px;height:52px;border:2px solid var(--line);border-radius:4px;box-shadow:1px 2px 3px rgba(0,0,0,.15);display:flex;align-items:center;justify-content:center;padding-left:44px;text-align:center;font-size:15px;line-height:20px;letter-spacing:1.5px;background:#fff}
.skill .ring{position:absolute;left:0;top:0;width:89px;height:89px;border-radius:50%;background:#fff;border:5px solid var(--purple-dark);box-shadow:0 0 0 2px var(--line);display:flex;align-items:center;justify-content:center}

/* contact */
.contact{left:0;top:3604px;width:1200px;height:597px;background:linear-gradient(135deg,var(--purple-dark) 0%,var(--purple) 50%,var(--purple-bright) 100%);clip-path:polygon(0 22%,50% 0,100% 22%,100% 100%,0 100%)}
.contact-title{top:3690px;width:1200px;text-align:center;color:#fff}
.field{left:160px;width:421px;height:50px;border:2px solid #fff;color:#fff;font-size:15px;letter-spacing:1.5px;padding:10px 14px}
.send{left:160px;top:4114px;width:121px;height:44px;background:#fff;font-family:"Poppins",sans-serif;font-size:16px;letter-spacing:3px;display:flex;align-items:center;justify-content:center}
.info{left:702px;display:flex;align-items:center;gap:24px;color:#fff;font-size:17px;letter-spacing:2px;white-space:nowrap}
.info .dot{width:62px;height:62px;border-radius:50%;background:#fff;display:flex;align-items:center;justify-content:center}

/* footer */
.footer{left:0;top:4201px;width:1200px;height:379px;background:var(--black);color:#fff}
.f-name{left:115px;top:4262px;font-family:"Poppins",sans-serif;font-weight:500;font-size:38px;letter-spacing:4px;line-height:50px;color:#fff;white-space:nowrap}
.f-tag{left:115px;top:4320px;font-family:"Poppins",sans-serif;font-weight:500;font-size:30px;letter-spacing:4px;color:#fff}
.f-social{left:115px;top:4406px;display:flex;gap:8px}
.f-social span{width:26px;height:26px;background:#fff;border-radius:4px}
.f-input{left:112px;top:4468px;width:330px;height:42px;background:#fff;color:var(--ink);font-size:13px;font-weight:600;padding:13px 16px}
.f-btn{left:442px;top:4468px;width:48px;height:42px;background:var(--purple-dark);display:flex;align-items:center;justify-content:center}
.f-col{color:#fff;font-size:15px;font-weight:600;letter-spacing:2px;line-height:31px}
.f-col h3{font-family:"Poppins",sans-serif;font-weight:500;font-size:19px;letter-spacing:3px;margin-bottom:2px}
.copy{top:4546px;width:1200px;text-align:center;color:#fff;font-size:12px;letter-spacing:.5px}
</style>
</head>
<body>

<header>
  <nav class="abs nav">
    <a href="#">Home</a><a href="#">About Me</a><a href="#">Services</a><a href="#">Contact Me</a><a href="#">Testimonilas</a><a href="#" class="login">LOGIN</a>
  </nav>
  <div class="abs brand"><div class="brand-name">LENA MORVATH</div><div class="brand-tag">OBM</div></div>
</header>

<section class="hero">
  <div class="abs hero-edge"></div>
  <div class="abs hero-photo" role="img" aria-label="Photo of a smiling woman working on a laptop at a desk, with a purple overlay"></div>
  <h1 class="abs hero-title"><span class="small">WELCOME TO</span><br><span class="big">ONLINE&nbsp; BUSINESS<br>MANAGER</span></h1>
  <div class="abs btn-light">GET STARTED</div>
  <svg class="abs arrow" style="left:25px;top:342px" viewBox="0 0 46 24"><path d="M44 12H4M14 3 4 12l10 9" fill="none" stroke="#fff" stroke-width="3"/></svg>
  <svg class="abs arrow" style="left:1125px;top:354px" viewBox="0 0 46 24"><path d="M2 12h40M32 3l10 9-10 9" fill="none" stroke="#fff" stroke-width="3"/></svg>
</section>

<section class="about">
  <h2 class="abs about-title">ABOUT ME</h2>
  <p class="abs about-text">Hi! I'm so excited that you have chosen to explore my portfolio. Helping businesses achieve their goals is my passion, and I'm thrilled that with my assistance you will have more time for your own passion project. I thrive while working independently, which means you can be confident when leaving tasks for me. The type of work that lights me up is anything involving organization and/or spreadsheets.</p>
  <div class="abs btn-dark">READ MORE</div>
  <div class="abs about-frame"></div>
  <div class="abs about-photo" role="img" aria-label="Portrait photo of the business owner in front of pink flowering shrubs"></div>
</section>

<section>
  <div class="abs services"></div>
  <h2 class="abs services-title">SERVICES</h2>
  <div class="abs service" style="left:108px;top:1540px">
    <div class="circle"><svg width="80" height="80" viewBox="0 0 80 80" fill="none" stroke="#4a2173" stroke-width="3"><circle cx="40" cy="20" r="10"/><rect x="18" y="40" width="44" height="28" rx="2"/><path d="M10 70h60"/><circle cx="40" cy="54" r="3"/></svg></div>
    <div class="label">VIRTUAL ASSISTANCE</div>
    <svg class="arrow" viewBox="0 0 46 24"><path d="M2 12h40M32 3l10 9-10 9" fill="none" stroke="#fff" stroke-width="3"/></svg>
  </div>
  <div class="abs service" style="left:360px;top:1540px">
    <div class="circle"><svg width="80" height="80" viewBox="0 0 80 80" fill="none" stroke="#4a2173" stroke-width="3"><rect x="10" y="12" width="18" height="14"/><rect x="54" y="10" width="16" height="16"/><rect x="56" y="44" width="14" height="14"/><path d="M22 50l22-12v28l-22-10z"/><path d="M12 70h44"/></svg></div>
    <div class="label">SOCIAL MEDIA &amp;<br>CONTENT MANAGEMENT</div>
    <svg class="arrow" viewBox="0 0 46 24"><path d="M2 12h40M32 3l10 9-10 9" fill="none" stroke="#fff" stroke-width="3"/></svg>
  </div>
  <div class="abs service" style="left:605px;top:1540px">
    <div class="circle"><svg width="80" height="80" viewBox="0 0 80 80" fill="none" stroke="#4a2173" stroke-width="3"><rect x="28" y="16" width="10" height="24"/><rect x="42" y="24" width="10" height="16"/><path d="M10 50h24l14 6 20-10v6L46 66H10z"/></svg></div>
    <div class="label">FINANCE MANAGEMENT</div>
    <svg class="arrow" viewBox="0 0 46 24"><path d="M2 12h40M32 3l10 9-10 9" fill="none" stroke="#fff" stroke-width="3"/></svg>
  </div>
  <div class="abs service" style="left:847px;top:1540px">
    <div class="circle"><svg width="80" height="80" viewBox="0 0 80 80" fill="none" stroke="#4a2173" stroke-width="3"><circle cx="40" cy="24" r="12"/><circle cx="40" cy="22" r="4"/><path d="M12 46l16-6 12 8 12-8 16 6-10 16H22z"/></svg></div>
    <div class="label">BUSINESS MANAGEMENT</div>
    <svg class="arrow" viewBox="0 0 46 24"><path d="M2 12h40M32 3l10 9-10 9" fill="none" stroke="#fff" stroke-width="3"/></svg>
  </div>
</section>

<section>
  <h2 class="abs rates-title">RATES AND PACKAGES</h2>
  <div class="abs rate" style="left:9px">
    <svg width="288" height="430" viewBox="0 0 288 430"><polygon points="0,0 288,0 288,330 144,430 0,330" fill="#4a2173"/><polygon points="2,8 286,8 286,312 144,402 2,312" fill="#faf8fc" stroke="#ddd"/><path d="M6,10 Q30,88 66,88 L222,88 Q258,88 282,10" fill="none" stroke="#4a2173" stroke-width="2.5"/></svg>
    <div class="head">HOURLY RATE</div>
    <div class="desc">For clients needing only occasional help</div>
    <div class="price">$40</div>
  </div>
  <div class="abs rate" style="left:309px">
    <svg width="288" height="430" viewBox="0 0 288 430"><polygon points="0,0 288,0 288,330 144,430 0,330" fill="#4a2173"/><polygon points="2,8 286,8 286,312 144,402 2,312" fill="#faf8fc" stroke="#ddd"/><path d="M6,10 Q30,88 66,88 L222,88 Q258,88 282,10" fill="none" stroke="#4a2173" stroke-width="2.5"/></svg>
    <div class="head">20 HOURS/MONTH</div>
    <div class="desc">Includes one 15 minute meeting per week</div>
    <div class="price">$700</div>
  </div>
  <div class="abs rate featured" style="left:609px">
    <svg width="288" height="430" viewBox="0 0 288 430"><polygon points="0,0 288,0 288,336 144,432 0,336" fill="#faf8fc" stroke="#ccc"/><polygon points="2,4 286,4 286,318 144,408 2,318" fill="#4a2173"/><path d="M6,6 Q30,88 66,88 L222,88 Q258,88 282,6" fill="none" stroke="#fff" stroke-width="2.5"/></svg>
    <div class="head">40 HOURS/MONTH</div>
    <div class="desc">Includes one 30 minute meeting per week</div>
    <div class="price">$1,300</div>
  </div>
  <div class="abs rate" style="left:909px">
    <svg width="288" height="430" viewBox="0 0 288 430"><polygon points="0,0 288,0 288,330 144,430 0,330" fill="#4a2173"/><polygon points="2,8 286,8 286,312 144,402 2,312" fill="#faf8fc" stroke="#ddd"/><path d="M6,10 Q30,88 66,88 L222,88 Q258,88 282,10" fill="none" stroke="#4a2173" stroke-width="2.5"/></svg>
    <div class="head">80 HOURS/MONTH</div>
    <div class="desc">Includes one 60 minute meeting per week</div>
    <div class="price">$2,400</div>
  </div>
</section>

<section>
  <div class="abs testi" role="img" aria-label="Misty mountain landscape with a purple overlay"></div>
  <h2 class="abs testi-title">TESTIMONIALS</h2>
  <p class="abs quote">When it became apparent that a project would take more time than I had, Lena stepped up to take on the required research. She was thorough and timely; able to meet a last-minute 12-hour deadline. I would highly recommend Lena to assist with your next project.</p>
  <p class="abs cite">Dana R. Owner, Ridgeline Roofing</p>
  <div class="abs avatar" role="img" aria-label="Client portrait photo"></div>
  <svg class="abs arrow" style="left:32px;top:2834px" viewBox="0 0 46 24"><path d="M44 12H4M14 3 4 12l10 9" fill="none" stroke="#fff" stroke-width="3"/></svg>
  <svg class="abs arrow" style="left:1130px;top:2850px" viewBox="0 0 46 24"><path d="M2 12h40M32 3l10 9-10 9" fill="none" stroke="#fff" stroke-width="3"/></svg>
</section>

<section>
  <h2 class="abs skills-title">WHAT I DO BEST</h2>
  <div class="abs skill" style="left:62px;top:3320px"><div class="pill">Content<br>Repurposing</div><div class="ring"><svg width="40" height="40" viewBox="0 0 40 40" fill="#4a2173"><rect x="8" y="6" width="22" height="28" rx="2"/><rect x="12" y="12" width="12" height="3" fill="#fff"/><rect x="12" y="18" width="12" height="3" fill="#fff"/></svg></div></div>
  <div class="abs skill" style="left:341px;top:3320px"><div class="pill">Data Entry</div><div class="ring"><svg width="40" height="40" viewBox="0 0 40 40" fill="#4a2173"><rect x="10" y="4" width="20" height="22" rx="2"/><rect x="6" y="28" width="28" height="8" rx="1"/></svg></div></div>
  <div class="abs skill" style="left:619px;top:3320px"><div class="pill">Email<br>Management</div><div class="ring"><svg width="40" height="40" viewBox="0 0 40 40"><rect x="5" y="10" width="30" height="22" fill="#4a2173"/><path d="M5 10l15 12 15-12" fill="none" stroke="#fff" stroke-width="2"/></svg></div></div>
  <div class="abs skill" style="left:898px;top:3320px"><div class="pill">Bookkeeping</div><div class="ring"><svg width="40" height="40" viewBox="0 0 40 40" fill="#4a2173"><rect x="8" y="4" width="24" height="32" rx="2"/><rect x="14" y="10" width="12" height="3" fill="#fff"/><rect x="14" y="17" width="12" height="3" fill="#fff"/><rect x="14" y="24" width="12" height="3" fill="#fff"/></svg></div></div>
  <div class="abs skill" style="left:62px;top:3428px"><div class="pill">Financial<br>Analytics</div><div class="ring"><svg width="40" height="40" viewBox="0 0 40 40" fill="#4a2173"><rect x="6" y="24" width="6" height="12"/><rect x="16" y="18" width="6" height="18"/><rect x="26" y="10" width="6" height="26"/></svg></div></div>
  <div class="abs skill" style="left:341px;top:3428px"><div class="pill">Graphic<br>Creations</div><div class="ring"><svg width="40" height="40" viewBox="0 0 40 40" fill="#4a2173"><circle cx="20" cy="17" r="10"/><rect x="15" y="28" width="10" height="7" rx="1"/></svg></div></div>
  <div class="abs skill" style="left:619px;top:3428px"><div class="pill">Project<br>Management</div><div class="ring"><svg width="40" height="40" viewBox="0 0 40 40" fill="#4a2173"><rect x="8" y="4" width="20" height="30" rx="2"/><circle cx="28" cy="28" r="8"/><circle cx="28" cy="28" r="3" fill="#fff"/></svg></div></div>
  <div class="abs skill" style="left:898px;top:3428px"><div class="pill">More<br>Awesomeness</div><div class="ring"><svg width="40" height="40" viewBox="0 0 40 40" fill="#4a2173"><rect x="5" y="5" width="13" height="13" rx="3"/><rect x="22" y="5" width="13" height="13" rx="3"/><rect x="5" y="22" width="13" height="13" rx="3"/><path d="M28.5 22v13M22 28.5h13" stroke="#4a2173" stroke-width="3"/></svg></div></div>
</section>

<section>
  <div class="abs contact"></div>
  <h2 class="abs contact-title">CONTACT US</h2>
  <div class="abs field" style="top:3794px">Name</div>
  <div class="abs field" style="top:3856px">Phone</div>
  <div class="abs field" style="top:3920px">Email</div>
  <div class="abs field" style="top:3983px;height:117px">Message</div>
  <div class="abs send">SEND</div>
  <div class="abs info" style="top:3801px"><span class="dot"><svg width="32" height="32" viewBox="0 0 32 32"><path d="M8 4l6 6-3 4c2 4 4 6 8 8l4-3 6 6-4 4C14 29 3 18 4 8z" fill="#4a2173"/></svg></span>555.014.2290</div>
  <div class="abs info" style="top:3883px"><span class="dot"><svg width="32" height="32" viewBox="0 0 32 32"><rect x="4" y="8" width="24" height="17" fill="none" stroke="#4a2173" stroke-width="2.5"/><path d="M4 8l12 10 12-10" fill="none" stroke="#4a2173" stroke-width="2.5"/></svg></span>lena.morvath@example.com</div>
  <div class="abs info" style="top:3960px"><span class="dot"></span>Lena Rae Morvath</div>
  <div class="abs info" style="top:4049px"><span class="dot"></span>/LenaMorvath07</div>
</section>

<footer>
  <div class="abs footer"></div>
  <div class="abs f-name">LENA MORVATH</div>
  <div class="abs f-tag">OBM</div>
  <div class="abs f-social"><span></span><span></span><span></span><span></span></div>
  <div class="abs f-input">Enter Your Email</div>
  <div class="abs f-btn"><svg width="30" height="22" viewBox="0 0 30 22"><rect x="2" y="2" width="26" height="18" fill="none" stroke="#fff" stroke-width="2"/><path d="M2 2l13 10 13-10M2 20l10-9M28 20l-10-9" fill="none" stroke="#fff" stroke-width="2"/></svg></div>
  <div class="abs f-col" style="left:558px;top:4266px"><h3>QUICK LINKS</h3>Home<br>About Me<br>Services<br>Testimonials<br>Contact Me</div>
  <div class="abs f-col" style="left:905px;top:4266px"><h3>OTHER LINKS</h3>Privacy Policy<br>Terms &amp; Conditions</div>
  <p class="abs copy">Copyright 2023 ©Lena Morvath .All rights reserved.</p>
</footer>

</body>
</html>
```